The most modern business card ever !!!

Our company call “Vendalo”. Vendalo is a technology company specialized in cruises solutions. Out main product is a platform to reserve cruises. This is a revolutionary platform that make easier to travel agencies and final users to reserve cruises across dozen companies like tibba, wernu, hpv, dgb, etc..We are a “start up”, with a young team of developers and we want to transmit it.. For it, we want something different, a modern business card that represent cruises and technology.. When someone receive this card, this person should say: wowww this is different… this is modern… this is a cruise related company..
- diferent, modern
- traditions business card

```html
<!DOCTYPE html>
<html lang="en">
<head>
<meta charset="utf-8">
<title>Vendalo business card</title>
<link rel="stylesheet" href="https://fonts.googleapis.com/css2?family=Michroma&family=Open+Sans:wght@400;600&display=swap">
<style>
  :root {
    --ink: #050505;
    --paper: #ffffff;
    --sky: #22a7e0;
    --sea: #0d4f6e;
    --stage: #e9e7e3;
    --text-dark: #111111;
  }
  * { box-sizing: border-box; margin: 0; padding: 0; }
  html, body { width: 1200px; height: 880px; overflow: hidden; }
  body { background: var(--stage); font-family: "Open Sans", Arial, sans-serif; position: relative; }

  .card {
    position: absolute;
    width: 560px; height: 320px;
    border-radius: 18px;
    overflow: hidden;
    box-shadow: 0 10px 28px rgba(0,0,0,.22);
  }
  .card-front { left: 90px; top: 80px; background: var(--ink); }
  .card-back { left: 550px; top: 470px; background: var(--paper); }

  .front-decor {
    position: absolute; left: 0; top: 0; width: 270px; height: 100%;
    background: linear-gradient(160deg, var(--sky) 0%, var(--sea) 60%, var(--ink) 100%);
  }
  .front-wordmark {
    position: absolute; right: 30px; top: 146px;
    font-family: "Michroma", sans-serif; font-size: 42px;
    color: var(--paper); letter-spacing: 1px;
  }

  .back-wordmark {
    position: absolute; left: 0; right: 0; top: 58px; text-align: center;
    font-family: "Michroma", sans-serif; font-size: 52px;
    color: var(--text-dark); letter-spacing: 1px;
  }
  .title-band {
    position: absolute; left: 0; right: 0; top: 172px; height: 38px;
    background: var(--sky);
    display: flex; align-items: center; justify-content: center; gap: 12px;
    color: var(--paper);
  }
  .person-name { font-family: "Michroma", sans-serif; font-size: 19px; }
  .band-divider { width: 1px; height: 24px; background: var(--paper); }
  .person-role { font-size: 15px; }

  .contacts {
    position: absolute; left: 0; right: 0; top: 222px; height: 80px;
    display: flex; align-items: stretch;
  }
  .contact-item {
    flex: 1; display: flex; flex-direction: column; align-items: center; justify-content: center; gap: 7px;
    font-size: 13.5px; color: var(--text-dark);
  }
  .contact-divider { width: 1px; margin: 12px 0; background: var(--sky); }
  .contact-icon { width: 36px; height: 36px; }
</style>
</head>
<body>

<section class="card card-front" aria-label="Card front">
  <div class="front-decor" role="img" aria-label="Decorative blue stripes evoking a cruise ship's wake on the sea"></div>
  <div class="front-wordmark">Vendalo</div>
</section>

<section class="card card-back" aria-label="Card back">
  <div class="back-wordmark">Vendalo</div>

  <div class="title-band">
    <span class="person-name">Lena Marlow</span>
    <span class="band-divider"></span>
    <span class="person-role">President</span>
  </div>

  <div class="contacts">
    <div class="contact-item">
      <svg class="contact-icon" viewBox="0 0 36 36" aria-hidden="true">
        <path d="M4 18 A14 14 0 0 1 32 18" fill="none" stroke="var(--sky)" stroke-width="2"/>
        <circle cx="18" cy="19" r="13" fill="var(--ink)"/>
        <rect x="13" y="11" width="10" height="16" rx="2" fill="none" stroke="var(--sky)" stroke-width="1.8"/>
        <circle cx="18" cy="24" r="1" fill="var(--sky)"/>
      </svg>
      <span class="contact-text">+(0) 44 321 7788</span>
    </div>
    <span class="contact-divider"></span>
    <div class="contact-item">
      <svg class="contact-icon" viewBox="0 0 36 36" aria-hidden="true">
        <path d="M4 18 A14 14 0 0 1 32 18" fill="none" stroke="var(--sky)" stroke-width="2"/>
        <circle cx="18" cy="19" r="13" fill="var(--ink)"/>
        <rect x="10" y="13" width="16" height="11" rx="1" fill="var(--sky)"/>
        <path d="M10 13 L18 20 L26 13" fill="none" stroke="var(--ink)" stroke-width="1.4"/>
      </svg>
      <span class="contact-text">hello@vendalomail.com</span>
    </div>
    <span class="contact-divider"></span>
    <div class="contact-item">
      <svg class="contact-icon" viewBox="0 0 36 36" aria-hidden="true">
        <path d="M4 18 A14 14 0 0 1 32 18" fill="none" stroke="var(--sky)" stroke-width="2"/>
        <circle cx="18" cy="19" r="13" fill="var(--ink)"/>
        <g fill="none" stroke="var(--sky)" stroke-width="1.4">
          <circle cx="18" cy="19" r="8"/>
          <ellipse cx="18" cy="19" rx="3.5" ry="8"/>
          <line x1="10" y1="19" x2="26" y2="19"/>
        </g>
      </svg>
      <span class="contact-text">www.vendalo-cruise.com</span>
    </div>
  </div>
</section>

</body>
</html>
```